New Business Card Design Project LORVANTI-Italy

we are LORVANTI-Italy
our company in the market for 3 years we are luxury cosmetic company and its about time for a facelift :)
i will like to have elegant luxurious and unique business card
that will give the person that get it a unique, luxurious and elegant impression
I'm VERY OPEN FOR NEW IDEAS , even duo i add a few files of things that i see on line and i like them

i add my logo as well
my website is LORVANTI.COM
(if you would like to see the main style that we have)

Target Market(s)

adult that have money :)

Industry/Entity Type

Business

Contact Information for Business Card

Name - Dario Lorvanti
Position - CEO and CO Founder
address - 4817 E Halvern
telephone - 555-384-1926
email - dario@lorvanti.com
fax - 555-384-1926
website - LORVANTI.COM

Colors
000000
959595
fbee3e
ffffff

Requirements
Must have
• big logo in GOLD color
• elegant look
• impressive
Nice to have
• not must but maybe classy pattern background
• not must but maybe emblem
• maybe clear plastic business card
Should not have
• colors
• images

```html
<!DOCTYPE html>
<html lang="en">
<head>
<meta charset="utf-8">
<title>LORVANTI Italy — Business Card</title>
<link rel="stylesheet" href="https://fonts.googleapis.com/css2?family=Cinzel:wght@500&family=Roboto:wght@400;700&display=swap">
<style>
  :root {
    --backdrop: #2b2b2b;
    --card: #1b1b1b;
    --gold: #d9b440;
    --white: #f4f4f4;
    --rule: #9a9a9a;
  }
  * { margin: 0; padding: 0; box-sizing: border-box; }
  html, body { width: 1200px; height: 900px; overflow: hidden; }
  body {
    background: var(--backdrop);
    display: flex;
    flex-direction: column;
    align-items: center;
    justify-content: center;
    gap: 40px;
    font-family: "Roboto", Arial, sans-serif;
  }
  .card {
    width: 700px;
    height: 400px;
    background: var(--card);
    position: relative;
    box-shadow: 0 6px 18px rgba(0,0,0,0.45);
  }

  /* Front */
  .card-front {
    display: flex;
    flex-direction: column;
    align-items: center;
    justify-content: center;
    gap: 22px;
  }
  .brand-circle {
    width: 96px;
    height: 96px;
    border: 3px solid var(--gold);
    border-radius: 50%;
  }
  .brand-name {
    font-family: "Cinzel", Georgia, serif;
    font-weight: 500;
    font-size: 44px;
    letter-spacing: 2px;
    color: var(--gold);
  }

  /* Back */
  .person {
    position: absolute;
    top: 108px;
    left: 0; right: 0;
    text-align: center;
  }
  .person-name {
    font-weight: 700;
    font-size: 26px;
    color: var(--gold);
    letter-spacing: 0.5px;
  }
  .person-role {
    margin-top: 6px;
    font-size: 16px;
    color: var(--white);
  }
  .contacts {
    position: absolute;
    left: 48px; right: 48px;
    bottom: 66px;
    display: flex;
    align-items: center;
    justify-content: space-between;
    color: var(--white);
    font-size: 17px;
  }
  .contact-group { display: flex; flex-direction: column; gap: 10px; }
  .contact-line { display: flex; align-items: center; gap: 10px; }
  .contact-group.right { align-items: flex-end; }
  .contact-group.center { align-items: center; gap: 8px; }
  .divider { width: 1px; height: 42px; background: var(--rule); }
  .icon { width: 18px; height: 18px; fill: var(--gold); flex: none; }
</style>
</head>
<body>

<section class="card card-front">
  <div class="brand-circle"></div>
  <div class="brand-name">LORVANTI</div>
</section>

<section class="card card-back">
  <div class="person">
    <div class="person-name">DARIO LORVANTI</div>
    <div class="person-role">CEO &amp; CO Founder</div>
  </div>

  <div class="contacts">
    <div class="contact-group left">
      <div class="contact-line">
        <svg class="icon" viewBox="0 0 24 24" aria-hidden="true"><path d="M6.6 10.8a15.1 15.1 0 0 0 6.6 6.6l2.2-2.2c.3-.3.7-.4 1-.2 1.1.4 2.3.6 3.6.6.6 0 1 .4 1 1V20c0 .6-.4 1-1 1A17 17 0 0 1 3 4c0-.6.4-1 1-1h3.5c.6 0 1 .4 1 1 0 1.3.2 2.5.6 3.6.1.3 0 .7-.2 1z"/></svg>
        <span>555-384-1926</span>
      </div>
      <div class="contact-line">
        <svg class="icon" viewBox="0 0 24 24" aria-hidden="true"><path d="M7 3h8l2 2v4H7zM3 10h18v8h-3v3H6v-3H3zm5 5v4h8v-4z"/></svg>
        <span>555-384-1926</span>
      </div>
    </div>

    <div class="divider"></div>

    <div class="contact-group center">
      <svg class="icon" viewBox="0 0 24 24" aria-hidden="true"><path d="M12 2a7 7 0 0 0-7 7c0 5.2 7 13 7 13s7-7.8 7-13a7 7 0 0 0-7-7zm0 9.5A2.5 2.5 0 1 1 12 6.5a2.5 2.5 0 0 1 0 5z"/></svg>
      <span>4817 E Halvern</span>
    </div>

    <div class="divider"></div>

    <div class="contact-group right">
      <div class="contact-line">
        <span>dario@lorvanti.com</span>
        <svg class="icon" viewBox="0 0 24 24" aria-hidden="true"><path d="M2 5h20v14H2zm2 2v.5l8 5 8-5V7z"/></svg>
      </div>
      <div class="contact-line">
        <span>LORVANTI.COM</span>
        <svg class="icon" viewBox="0 0 24 24" aria-hidden="true"><path d="M12 2a10 10 0 1 0 0 20 10 10 0 0 0 0-20zm0 2c.9 1.2 1.6 2.6 2 4h-4c.4-1.4 1.1-2.8 2-4zM4.3 14a8 8 0 0 1 0-4h3.4a16 16 0 0 0 0 4zm.8 2h3c.3 1.3.8 2.5 1.4 3.6A8 8 0 0 1 5.1 16zm3-8h-3a8 8 0 0 1 4.4-3.6C8.9 5.5 8.4 6.7 8.1 8zM12 20c-.9-1.2-1.6-2.6-2-4h4c-.4 1.4-1.1 2.8-2 4zm2.3-6H9.7a14 14 0 0 1 0-4h4.6a14 14 0 0 1 0 4zm.2 5.6c.6-1.1 1.1-2.3 1.4-3.6h3a8 8 0 0 1-4.4 3.6zM16.3 14a16 16 0 0 0 0-4h3.4a8 8 0 0 1 0 4z"/></svg>
      </div>
    </div>
  </div>
</section>

</body>
</html>
```